Business Card for Polygraph business in Africa

Business Card . Polygraph Examiner based in Tanzania, East Africa.
Business Card will be used to disseminate contact information to potential clients.
It should convey that I am a professional specifically in the polygraph field and perform my work with integrity.

I have attached the business card that I'm currently using, which I threw together myself initially. It's not professional enough.

Target Market(s)

Banks, Accounting Firms, Government Ministries, Gas, Oil, & Gemstone Mining Concerns, Wildlife Conservation NGOs, International companies located in East Africa.

Industry/Entity Type

Business

Contact Information for Business Card

Veritrace Kilonga
Miriam Holloway
PO Box 48317
Arusha, Tanzania
+255 612 839 274
miriamholloway@postvale.example

Colors
00a990
f37122
faa54b

Requirements
Must have
• - Veritrace Kilonga (with the word "Polygraph" being more prominent than the word "Tanzania")
• - Forensic Examinations
• - Employment Screening
• - Should contain a logo of the Continental Truthline Society (of which I'm a member)
• - I would like an accent design (such as the polygraph "squiggles" of a cardio tracing or such as that)
• - My contact information (less prominent, but large enough to read legibly). I would also consider putting the contact information on the second side of the card.
Nice to have
• My color suggestions are changeable.
Should not have
• Anything "cutesy" or "cartoonish"

```html
<!DOCTYPE html>
<html lang="en">
<head>
<meta charset="utf-8">
<title>Veritrace Kilonga – Business Card</title>
<link rel="stylesheet" href="https://fonts.googleapis.com/css2?family=Roboto:wght@400;500;700&family=Roboto+Condensed:wght@700&display=swap">
<style>
  :root {
    --backdrop: #2a2a2c;
    --card: #1d1d1f;
    --card-edge: #262628;
    --brand-blue: #1a62c9;
    --ink-white: #f4f4f4;
    --ink-grey: #6e6e72;
    --rule-grey: #8a8a8e;
  }
  * { box-sizing: border-box; margin: 0; padding: 0; }
  html, body { width: 1200px; height: 900px; overflow: hidden; }
  body {
    background: var(--backdrop);
    font-family: "Roboto", Arial, sans-serif;
    color: var(--ink-white);
    position: relative;
  }
  .card {
    position: absolute;
    left: 270px;
    width: 660px;
    height: 340px;
    background: var(--card);
    border: 1px solid var(--card-edge);
    box-shadow: 0 10px 30px rgba(0,0,0,0.45);
    overflow: hidden;
  }
  .card--front { top: 70px; }
  .card--back { top: 480px; }

  /* Front */
  .brand {
    position: absolute;
    top: 92px;
    left: 0; right: 0;
    display: flex;
    align-items: center;
    justify-content: center;
    gap: 18px;
  }
  .brand__dot {
    width: 46px; height: 46px;
    border-radius: 50%;
    background: var(--brand-blue);
  }
  .brand__name {
    font-weight: 700;
    font-size: 46px;
    letter-spacing: 0.5px;
    color: var(--ink-white);
  }
  .services {
    position: absolute;
    top: 222px;
    left: 0; right: 0;
    text-align: center;
    font-size: 17px;
    color: var(--ink-white);
  }
  .services__sep {
    display: inline-block;
    width: 7px; height: 7px;
    border-radius: 50%;
    background: var(--brand-blue);
    margin: 0 12px;
    vertical-align: middle;
  }

  /* Back */
  .holder {
    position: absolute;
    top: 124px;
    left: 20px;
    width: 272px;
    text-align: right;
  }
  .holder__name {
    font-family: "Roboto Condensed", "Arial Narrow", sans-serif;
    font-weight: 700;
    font-size: 32px;
    line-height: 36px;
    color: var(--brand-blue);
    letter-spacing: 0.3px;
  }
  .holder__company {
    font-weight: 700;
    font-size: 18px;
    color: var(--ink-grey);
    letter-spacing: 0.8px;
    margin-top: 2px;
  }
  .divider {
    position: absolute;
    left: 312px;
    top: 116px;
    width: 2px;
    height: 100px;
    background: var(--rule-grey);
  }
  .contacts {
    position: absolute;
    left: 334px;
    top: 122px;
    list-style: none;
    font-size: 16px;
    line-height: 30px;
  }
  .contacts li { display: flex; align-items: center; gap: 10px; white-space: nowrap; }
  .contacts svg { width: 16px; height: 16px; fill: var(--brand-blue); flex: none; }
  .member-badge {
    position: absolute;
    top: 18px;
    right: 24px;
    width: 84px; height: 84px;
    border-radius: 50%;
    border: 4px solid var(--brand-blue);
    box-shadow: inset 0 0 0 6px var(--card), inset 0 0 0 8px var(--brand-blue);
  }
  .address {
    position: absolute;
    left: 60px;
    bottom: 40px;
    display: flex;
    align-items: center;
    gap: 8px;
    font-size: 17px;
  }
  .address svg { width: 16px; height: 20px; fill: var(--brand-blue); }
</style>
</head>
<body>

<section class="card card--front">
  <div class="brand">
    <span class="brand__dot"></span>
    <span class="brand__name">Veritrace Kilonga</span>
  </div>
  <p class="services">Forensic Examinations<span class="services__sep"></span>Employment Screening</p>
</section>

<section class="card card--back">
  <div class="member-badge" role="img" aria-label="Continental Truthline Society membership badge"></div>

  <div class="holder">
    <h1 class="holder__name">MIRIAM HOLLOWAY</h1>
    <p class="holder__company">VERITRACE KILONGA</p>
  </div>

  <div class="divider"></div>

  <ul class="contacts">
    <li>
      <svg viewBox="0 0 16 16" aria-hidden="true"><path d="M3.6 1.2l2.2 2.6-1.3 1.7c.9 2 2.3 3.5 4.2 4.4l1.7-1.3 2.6 2.2-1 2.8C6.5 13.4 2.6 9.5 1 3.6z"/></svg>
      <span>+255 612 839 274</span>
    </li>
    <li>
      <svg viewBox="0 0 16 16" aria-hidden="true"><path d="M1 3h14v10H1z"/><path d="M1 3h14L8 8.6z" fill="#1d1d1f"/></svg>
      <span>miriamholloway@postvale.example</span>
    </li>
    <li>
      <svg viewBox="0 0 16 16" aria-hidden="true"><circle cx="8" cy="8" r="7"/><path d="M4 6c2 0 2 2 4 2s1 3 3 3" stroke="#1d1d1f" stroke-width="1.4" fill="none"/></svg>
      <span>www.miriamholloway.example</span>
    </li>
  </ul>

  <div class="address">
    <svg viewBox="0 0 16 20" aria-hidden="true"><path d="M8 0a7 7 0 0 0-7 7c0 5 7 13 7 13s7-8 7-13a7 7 0 0 0-7-7zm0 10a3 3 0 1 1 0-6 3 3 0 0 1 0 6z"/></svg>
    <span>PO Box 48317, Arusha, Tanzania</span>
  </div>
</section>

</body>
</html>
```